4th Generation Family Business Needs a New Card Design!

We are a family owned 4th Generation company. We are based in the Sydney, Australia area and we are desperately in need of a more modern and classy card. We are monumental masons who design, supply & erect lasting memorials throughout cemeteries in Sydney. Our customers are normally in a period of grieving. I have attached logo files that will need to be implemented on the card. Company was established 1935. Australian Owned and Operated. Card needs to be designed to PIXO.com specification.

Target Market(s)

Our target market is based upon people that a grieving for family members that have passed away. We also deal with alot of companies that own and operate cemeteries.

Industry/Entity Type

Business

Contact Information for Business Card

Simon Harcourt, Operations Manager, 0417293086, simon@harcourtmemorials.com.au
Lewis Harcourt, Director, 0491630572, lewis@harcourtmemorials.com.au
Phone # 02 9561 3048
Website: www.harcourtmemorials.com.au
Address: Suite 17, 8 Palfrey Lane, West Carlow, Sydney NSW 2156

Font styles to use
Serif
Decorative
Script

Requirements
Must have
• Would like to see the logo nicely implemented with a modern design. Embossed lettering would be a nice additive.

```html
<!DOCTYPE html>
<html lang="en">
<head>
<meta charset="utf-8">
<title>Harcourt Memorials — Business Card</title>
<link rel="stylesheet" href="https://fonts.googleapis.com/css2?family=Arimo:wght@400;700&display=swap">
<style>
  :root {
    --backdrop: #2f2a27;
    --card: #151515;
    --card-edge: #202020;
    --gold: #e8b321;
    --white: #f2f2f2;
    --deep-grey: #3c3c3c;
    --mid-grey: #6a6a6a;
    --rule: #5a5a5a;
  }
  * { margin: 0; padding: 0; box-sizing: border-box; }
  html, body {
    width: 1200px;
    height: 864px;
    overflow: hidden;
    background: var(--backdrop);
    font-family: "Arimo", Arial, sans-serif;
  }
  .stage {
    position: relative;
    width: 1200px;
    height: 864px;
  }
  .card {
    position: absolute;
    width: 530px;
    height: 303px;
    background: var(--card);
    border: 1px solid var(--card-edge);
  }
  .card--back { left: 50px; top: 130px; }
  .card--front { left: 620px; top: 420px; }

  /* Back side */
  .back-brand {
    position: absolute;
    left: 0; right: 0; top: 118px;
    text-align: center;
    color: var(--deep-grey);
    font-size: 30px;
    font-weight: 700;
    letter-spacing: 3px;
    text-transform: uppercase;
  }
  .back-web {
    position: absolute;
    left: 0; right: 0; top: 176px;
    text-align: center;
    color: var(--mid-grey);
    font-size: 14px;
    letter-spacing: 0.5px;
  }

  /* Front side */
  .front-brand {
    position: absolute;
    left: 30px; top: 120px;
    width: 210px;
    display: flex;
    align-items: center;
    gap: 10px;
    color: var(--white);
    font-size: 19px;
    font-weight: 700;
    line-height: 1.2;
    text-transform: uppercase;
    letter-spacing: 1px;
  }
  .front-brand .mark-square {
    flex: none;
    width: 16px; height: 16px;
    background: var(--gold);
  }
  .divider {
    position: absolute;
    left: 262px; top: 40px;
    width: 1px; height: 150px;
    background: var(--rule);
  }
  .details {
    position: absolute;
    left: 282px; top: 44px;
    color: var(--white);
    font-size: 14px;
    line-height: 1.3;
  }
  .details .name {
    color: var(--gold);
    font-size: 19px;
    font-weight: 700;
  }
  .details .role { font-size: 16px; margin-bottom: 12px; }
  .details .address { margin-bottom: 6px; }
  .contact-list { list-style: none; }
  .contact-list li {
    display: flex;
    align-items: center;
    gap: 8px;
    margin-bottom: 3px;
  }
  .contact-list svg { width: 13px; height: 13px; flex: none; }
</style>
</head>
<body>
<main class="stage">

  <section class="card card--back" aria-label="Card back">
    <div class="back-brand">Harcourt Memorials</div>
    <div class="back-web">www.harcourtmemorials.com.au</div>
  </section>

  <section class="card card--front" aria-label="Card front">
    <div class="front-brand">
      <span class="mark-square"></span>
      <span>Harcourt Memorials</span>
    </div>
    <div class="divider"></div>
    <div class="details">
      <div class="name">Simon Harcourt</div>
      <div class="role">Operations Manager</div>
      <div class="address">Suite 17, 8 Palfrey Lane<br>West Carlow, Sydney NSW 2156</div>
      <ul class="contact-list">
        <li>
          <svg viewBox="0 0 16 16" aria-hidden="true"><path fill="var(--gold)" d="M3 1h3l1.5 4-2 1.3a9 9 0 0 0 4.2 4.2L11 8.5l4 1.5v3a2 2 0 0 1-2 2A12 12 0 0 1 1 3a2 2 0 0 1 2-2z"/></svg>
          <span>02 9561 3048</span>
        </li>
        <li>
          <svg viewBox="0 0 16 16" aria-hidden="true"><rect x="4" y="1" width="8" height="14" rx="1.5" fill="none" stroke="var(--gold)" stroke-width="1.8"/><circle cx="8" cy="12.3" r="0.9" fill="var(--gold)"/></svg>
          <span>0417293086</span>
        </li>
        <li>
          <svg viewBox="0 0 16 16" aria-hidden="true"><rect x="1" y="3" width="14" height="10" fill="var(--gold)"/><path d="M1 3l7 5.5L15 3" fill="none" stroke="var(--card)" stroke-width="1.4"/></svg>
          <span>simon@harcourtmemorials.com.au</span>
        </li>
        <li>
          <svg viewBox="0 0 16 16" aria-hidden="true"><circle cx="8" cy="8" r="7" fill="var(--gold)"/><path d="M1 8h14M8 1c-3 3.5-3 10.5 0 14M8 1c3 3.5 3 10.5 0 14" fill="none" stroke="var(--card)" stroke-width="1"/></svg>
          <span>www.harcourtmemorials.com.au</span>
        </li>
      </ul>
    </div>
  </section>

</main>
</body>
</html>
```